Custom Manufacturing Company square space website design

I own a custom manufacturing company that uses precision cutting technology to manufacture project components over a couple industries. We have an industrial CNC router and state of the art edge bander and cut a lot of cabinetry components for cabinet shops, builders, closet companies, ect. We offer design and assembly for any cabinetry or can build cabinets to spec. We also cut components for other industries out of wood, plastics, acryclics, ect. We offer design engineering services, product development protype services. we have a 3D printer farm. We want our communicate trust, dependability, and the value we place on client relationships.

We essentially want a credibility website. Landing page and drops downs for services we offer, capabilites, about us, contact

```html
<!DOCTYPE html>
<html lang="en">
<head>
<meta charset="utf-8">
<title>Northline CNC</title>
<link href="https://fonts.googleapis.com/css2?family=Audiowide&family=Lato:wght@400;700&display=swap" rel="stylesheet">
<style>
:root{
  --ink:#111111;
  --white:#ffffff;
  --muted:#555555;
  --grey:#8a8a8a;
  --line:#cfcfcf;
  --field:#f7f7f7;
  --dark:#1a1a1a;
  --footer:#0d0d0d;
}
*{box-sizing:border-box;margin:0;padding:0}
html,body{width:1200px;height:3480px;overflow:hidden}
body{position:relative;background:var(--white);color:var(--ink);font-family:"Lato",sans-serif}
.abs{position:absolute}
.display{font-family:"Audiowide",sans-serif;text-transform:uppercase}
.photo{position:absolute}
.btn-dark{position:absolute;background:var(--ink);color:var(--white);font-family:"Audiowide",sans-serif;display:flex;align-items:center;justify-content:center;text-transform:uppercase}

/* header */
.call-icon{left:111px;top:40px;width:42px;height:42px;border-radius:50%;background:var(--ink);box-shadow:0 2px 6px rgba(0,0,0,.3);display:flex;align-items:center;justify-content:center}
.call-label{left:165px;top:42px;font-size:13px;color:var(--grey)}
.call-number{left:165px;top:66px;font-size:15px;color:var(--ink)}
.brand{left:450px;top:58px;width:300px;text-align:center;font-size:20px;letter-spacing:4px;color:var(--ink)}
.brand-square{left:586px;top:24px;width:28px;height:28px;border:2px solid var(--ink)}

/* social links: invented network names with a plain dot */
.social-links{display:flex;gap:10px;align-items:center}
.social-links a{display:flex;align-items:center;gap:4px;font-family:"Lato",sans-serif;font-weight:700;font-size:12px;color:var(--ink);text-decoration:none}
.social-links a::before{content:"";width:9px;height:9px;border-radius:50%;background:currentColor;display:block}
.social-links.on-dark a{color:var(--white)}
.header-social{left:899px;top:54px}

.nav-rule{left:111px;top:124px;width:978px;height:1px;background:var(--line)}
.nav{left:111px;top:146px;width:978px;display:flex;justify-content:space-between;font-size:13px}
.nav a{color:var(--ink);text-decoration:none;padding:0 4px}
.nav i{width:1px;height:20px;background:var(--line);display:block}

/* hero */
.hero{left:0;top:188px;width:1200px;height:597px;background:linear-gradient(180deg,#4a4a4a 0%,#3a3a3a 45%,#2b2b2b 100%)}
.hero-square{left:484px;top:277px;width:229px;height:162px;border:5px solid var(--white)}
.hero-title{left:0;top:478px;width:1200px;text-align:center;color:var(--white);font-size:58px;letter-spacing:14px}
.hero-sub{left:0;top:540px;width:1200px;text-align:center;color:var(--white);font-size:38px;letter-spacing:10px}
.hero-btn{left:501px;top:605px;width:199px;height:54px;border:2px solid var(--white);background:#111;color:var(--white);font-family:"Audiowide",sans-serif;font-size:16px;display:flex;align-items:center;justify-content:center}
.arrow{width:32px;height:32px;border-radius:50%;background:var(--white);display:flex;align-items:center;justify-content:center;top:469px}

/* about */
.about-text{left:639px;top:935px;width:450px;font-size:14.5px;line-height:27.5px;color:var(--muted);text-align:justify}
.about-text p+p{margin-top:27px}
.section-head{font-size:30px;color:var(--ink)}
.section-sub{font-size:16px;color:var(--grey);display:flex;align-items:center;gap:10px}
.section-sub::before{content:"";width:130px;height:1px;background:var(--grey);display:block}

/* services */
.service-card{box-shadow:0 0 0 1px #bbb}
.service-label{position:absolute;background:var(--white);box-shadow:0 4px 12px rgba(0,0,0,.12);font-family:"Audiowide",sans-serif;font-size:15px;display:flex;align-items:center;justify-content:center;text-transform:uppercase}

/* printer farm */
.farm{left:0;top:1867px;width:1200px;height:512px;background:linear-gradient(90deg,#2e2e2e 0%,#1f1f1f 50%,#161616 100%)}
.farm-text{left:111px;top:2010px;width:490px;color:var(--white);font-size:14px;line-height:29px}
.farm-list{left:111px;top:2136px;color:var(--white);font-size:16px;font-weight:700;list-style:none}
.farm-list li{display:flex;align-items:center;gap:10px;height:37px}
.accent-block{left:980px;top:1894px;width:150px;height:150px;background:#3a3a3a}

/* contact */
.field{position:absolute;background:var(--field);box-shadow:0 2px 6px rgba(0,0,0,.08);font-size:14px;color:#555;padding:18px 17px}
.contact-item{position:absolute;display:flex;gap:12px}
.contact-item .ic{width:26px;height:26px;border-radius:50%;background:var(--ink);display:flex;align-items:center;justify-content:center;flex:none}
.contact-item b{font-size:15px;display:block}
.contact-item span{font-size:13px}

/* footer */
.footer{left:0;top:2983px;width:1200px;height:497px;background:var(--footer);color:var(--white)}
.footer-col h4{font-family:"Audiowide",sans-serif;font-weight:400;font-size:15px;margin-bottom:18px;text-transform:uppercase}
.footer-col ul{list-style:none;font-size:15px;line-height:27.5px}
.footer-col li::before{content:"→ ";font-size:12px}
</style>
</head>
<body>

<!-- header -->
<div class="abs call-icon"><svg width="20" height="20" viewBox="0 0 24 24"><path fill="#fff" d="M6.6 10.8a15 15 0 006.6 6.6l2.2-2.2a1 1 0 011-.25 11.4 11.4 0 003.6.57 1 1 0 011 1V20a1 1 0 01-1 1A17 17 0 013 4a1 1 0 011-1h3.5a1 1 0 011 1c0 1.25.2 2.45.57 3.57a1 1 0 01-.25 1z"/></svg></div>
<div class="abs call-label display">Call now:</div>
<div class="abs call-number display">+1 555 010 0199</div>
<div class="abs brand-square"></div>
<div class="abs brand display">Northline CNC</div>
<div class="abs social-links header-social"><a>Sharo</a><a>Pixa</a><a>Chirp</a><a>Loop</a></div>
<div class="abs nav-rule"></div>
<nav class="abs nav display">
  <a>Home</a><i></i><a>Services we offer</a><i></i><a>Capabilities</a><i></i><a>About us</a><i></i><a>Contact us</a>
</nav>

<!-- hero -->
<section class="abs hero" role="img" aria-label="Photo of a modern kitchen with grey cabinetry, dimmed"></section>
<div class="abs hero-square"></div>
<div class="abs hero-title display">Northline</div>
<div class="abs hero-sub display">CNC</div>
<div class="abs hero-btn">GET STARTED</div>
<div class="abs arrow" style="left:32px"><svg width="14" height="14" viewBox="0 0 14 14"><path d="M9 2L4 7l5 5" stroke="#111" stroke-width="2.5" fill="none"/></svg></div>
<div class="abs arrow" style="left:1133px"><svg width="14" height="14" viewBox="0 0 14 14"><path d="M5 2l5 5-5 5" stroke="#111" stroke-width="2.5" fill="none"/></svg></div>

<!-- about -->
<div class="photo" style="left:111px;top:870px;width:130px;height:180px;background:linear-gradient(160deg,#9fc7d9,#e07a1f)" role="img" aria-label="Orange drawer cabinet with a lamp"></div>
<div class="photo" style="left:249px;top:870px;width:322px;height:180px;background:linear-gradient(135deg,#1d3f8a,#2c7fc4 55%,#5a3a50)" role="img" aria-label="3D printer printing a part"></div>
<div class="photo" style="left:111px;top:1058px;width:322px;height:178px;background:linear-gradient(135deg,#d8d8d8,#a9a9a9)" role="img" aria-label="White kitchen cabinets"></div>
<div class="photo" style="left:441px;top:1058px;width:130px;height:178px;background:linear-gradient(180deg,#8f8f88,#5b5f55)" role="img" aria-label="Craftsman working on wood parts"></div>
<h2 class="abs display section-head" style="left:638px;top:864px">About Northline</h2>
<div class="abs section-sub display" style="left:760px;top:902px">CNC</div>
<div class="abs about-text">
  <p>Nam libero tempore, cum soluta nobis est eligendi optio cumque nihil impedit quo minus id quod maxime placeat facere possimus, omnis voluptas assumenda est, omnis dolor repellendus. Temporius autem quibusdam et aut officiis debitis aut rerum necessitatibus t voluptates repudiandae sint et molestiae non recusandae.</p>
  <p>Itaque earum rerum hic tenetur a sapiente delectus, ut aut reiciendis voluptatibus maiores alias consequatur aut perferendis doloribus asperiores repellat.</p>
</div>
<div class="btn-dark" style="left:640px;top:1191px;width:141px;height:42px;font-size:14px">Read more</div>

<!-- services -->
<h2 class="abs display section-head" style="left:0;width:1200px;text-align:center;top:1330px">Services we offer</h2>
<div class="abs section-sub display" style="left:574px;top:1371px;font-size:15px">Service</div>
<div class="photo service-card" style="left:119px;top:1417px;width:465px;height:341px;background:linear-gradient(135deg,#e6e6e6,#b5b5b5)" role="img" aria-label="Engineer measuring a part over technical drawings"></div>
<div class="photo service-card" style="left:616px;top:1417px;width:465px;height:341px;background:linear-gradient(90deg,#5c6a72 0%,#5c6a72 28%,#c8a074 40%,#a36a3c 62%,#8a5530 80%,#b08a6a 100%)" role="img" aria-label="Row of wood and painted cabinet door samples"></div>
<div class="service-label" style="left:159px;top:1731px;width:387px;height:56px">Design engineering services</div>
<div class="service-label" style="left:656px;top:1731px;width:387px;height:56px">Product development prototype</div>

<!-- printer farm -->
<section class="abs farm" role="img" aria-label="Dark photo of 3D printed parts"></section>
<h2 class="abs display" style="left:108px;top:1932px;font-size:30px;color:#fff">3D printer farm</h2>
<div class="abs section-sub display" style="left:180px;top:1976px;color:#ccc">Northline</div>
<div class="farm-text abs">We own a custom manufacturing company that uses precision cutting technology to manufacture project components over a couple industries. We have an industrial CNC router and state of the art edge bander and cut a lot of cabinetry components for cabinet shops, builders, closet companies, ect.</div>
<ul class="abs farm-list">
  <li><svg width="14" height="12" viewBox="0 0 14 12"><path d="M1 6l4 4 8-9" stroke="#fff" stroke-width="2.5" fill="none"/></svg>Itaque earum rerum hic tenetur a sapiente</li>
  <li><svg width="14" height="12" viewBox="0 0 14 12"><path d="M1 6l4 4 8-9" stroke="#fff" stroke-width="2.5" fill="none"/></svg>Coluptatibus maiores alias consequatur</li>
  <li><svg width="14" height="12" viewBox="0 0 14 12"><path d="M1 6l4 4 8-9" stroke="#fff" stroke-width="2.5" fill="none"/></svg>Perferendis doloribus asperiores repellat</li>
</ul>
<div class="abs display" style="left:111px;top:2268px;width:143px;height:47px;border:2px solid #fff;color:#fff;font-size:14px;display:flex;align-items:center;justify-content:center">Learn more</div>
<div class="abs accent-block" role="img" aria-label="Decorative accent area"></div>
<div class="photo" style="left:657px;top:1940px;width:429px;height:495px;border:3px solid #fff;box-shadow:0 4px 14px rgba(0,0,0,.25);background:linear-gradient(180deg,#6f8fa3 0%,#a9b9c3 45%,#e8e6e2 100%)" role="img" aria-label="Two people watching a 3D printer at work"></div>

<!-- contact -->
<h2 class="abs display section-head" style="left:0;width:1200px;text-align:center;top:2506px">Get in touch with us</h2>
<div class="abs section-sub display" style="left:550px;top:2551px;font-size:15px">Contact us</div>
<h3 class="abs display" style="left:111px;top:2599px;font-size:17px;font-weight:400">Let's talk</h3>
<p class="abs" style="left:113px;top:2628px;width:370px;font-size:13.5px;line-height:26px;color:var(--muted)">Itaque earum rerum hic tenetur a sapiente delectus, ut aut reiciendis voluptatibus maiores alias consequatur aut perferendis doloribus asperiores repellat.</p>
<p class="abs" style="left:111px;top:2718px;font-size:17px;font-weight:700">Stay Tuned with is on Social Networks</p>
<div class="contact-item" style="left:111px;top:2755px"><div class="ic"><svg width="13" height="13" viewBox="0 0 24 24"><path fill="#fff" d="M6.6 10.8a15 15 0 006.6 6.6l2.2-2.2a1 1 0 011-.25 11.4 11.4 0 003.6.57 1 1 0 011 1V20a1 1 0 01-1 1A17 17 0 013 4a1 1 0 011-1h3.5a1 1 0 011 1c0 1.25.2 2.45.57 3.57a1 1 0 01-.25 1z"/></svg></div><div><b>Phone:</b><span>+1 555 010 0199</span></div></div>
<div class="contact-item" style="left:276px;top:2755px"><div class="ic"><svg width="13" height="10" viewBox="0 0 14 10"><rect width="14" height="10" rx="1" fill="#fff"/><path d="M0 1l7 5 7-5" stroke="#111" stroke-width="1.3" fill="none"/></svg></div><div><b>Email Us:</b><span>hello@northlinecnc.com</span></div></div>
<div class="abs social-links" style="left:113px;top:2838px"><a>Sharo</a><a>Pixa</a><a>Chirp</a><a>Loop</a></div>
<div class="field" style="left:513px;top:2603px;width:282px;height:49px">First Name</div>
<div class="field" style="left:807px;top:2603px;width:282px;height:49px">Your Email</div>
<div class="field" style="left:513px;top:2666px;width:282px;height:48px">Your Phone</div>
<div class="field" style="left:807px;top:2666px;width:282px;height:48px">Address</div>
<div class="field" style="left:513px;top:2730px;width:576px;height:110px">Message</div>
<div class="btn-dark" style="left:515px;top:2874px;width:140px;height:43px;font-size:14px">Submit</div>

<!-- footer -->
<footer class="abs footer"></footer>
<div class="abs display" style="left:183px;top:3058px;font-size:20px;color:#fff">Subscribe for joining us</div>
<div class="abs" style="left:574px;top:3047px;width:441px;height:45px;background:#fff;border:2px solid #fff;display:flex">
  <div style="flex:1;font-size:12px;color:#777;padding:13px 20px">Enter Your Email</div>
  <div style="width:147px;background:#111;color:#fff;font-size:14px;display:flex;align-items:center;justify-content:center">SUBSCRIBE</div>
</div>
<div class="abs" style="left:111px;top:3137px;width:978px;height:1px;background:#444"></div>

<div class="abs footer-col" style="left:111px;top:3203px;color:#fff">
  <h4>Contact us</h4>
  <div style="display:flex;gap:10px;font-size:15px;line-height:23px"><svg width="12" height="16" viewBox="0 0 12 16" style="margin-top:5px"><path fill="#fff" d="M6 0a6 6 0 00-6 6c0 4.5 6 10 6 10s6-5.5 6-10a6 6 0 00-6-6zm0 8.5A2.5 2.5 0 116 3.5a2.5 2.5 0 010 5z"/></svg><div>Northline CNC<br>United states</div></div>
  <div style="display:flex;gap:10px;font-size:15px;margin-top:20px;align-items:center"><svg width="13" height="13" viewBox="0 0 24 24"><path fill="#fff" d="M6.6 10.8a15 15 0 006.6 6.6l2.2-2.2a1 1 0 011-.25 11.4 11.4 0 003.6.57 1 1 0 011 1V20a1 1 0 01-1 1A17 17 0 013 4a1 1 0 011-1h3.5a1 1 0 011 1c0 1.25.2 2.45.57 3.57a1 1 0 01-.25 1z"/></svg>+1 555 010 0199</div>
  <div style="display:flex;gap:10px;font-size:15px;margin-top:20px;align-items:center"><svg width="13" height="10" viewBox="0 0 14 10"><rect width="14" height="10" rx="1" fill="#fff"/><path d="M0 1l7 5 7-5" stroke="#0d0d0d" stroke-width="1.3" fill="none"/></svg>hello@northlinecnc.com</div>
</div>
<div class="abs footer-col" style="left:416px;top:3203px;color:#fff">
  <h4>Quick links</h4>
  <ul><li>Home</li><li>Services</li><li>About Us</li><li>Capabilities</li><li>Contact Us</li></ul>
</div>
<div class="abs footer-col" style="left:659px;top:3203px;color:#fff">
  <h4>Help center</h4>
  <ul><li>FAQ</li><li>Terms</li><li>Privacy Policy</li><li>Support Center</li><li>Conditions</li></ul>
</div>
<div class="abs" style="left:970px;top:3208px;width:38px;height:38px;border:2px solid #fff"></div>
<div class="abs display" style="left:880px;top:3272px;width:220px;text-align:center;color:#fff;font-size:18px;letter-spacing:3px">Northline CNC</div>
<div class="abs social-links on-dark" style="left:893px;top:3344px"><a>Sharo</a><a>Pixa</a><a>Chirp</a><a>Loop</a></div>

<div class="abs" style="left:113px;top:3428px;width:330px;height:1px;background:#777"></div>
<div class="abs" style="left:745px;top:3428px;width:342px;height:1px;background:#777"></div>
<div class="abs" style="left:443px;top:3420px;width:302px;text-align:center;font-size:11px;color:#fff">Copyrights@2023 Northline CNC. All Rights Reserved</div>

</body>
</html>
```